Health and Wellness company needs flyer to promote free seminar

Corvella Motion studio is a health and wellness company that offers an exercise program designed by physical therapists to help relieve pain and improve mobility. Our business is a new concept that is not well understood by the public. In order to promote our business we offer a free seminar where we present information regarding the underlying cause of pain and tightness. During the seminar we also perform a posture screen and movement testing for all participants.

Target Market(s)

Mostly healthy and active women ages 25-65

Industry/Entity Type

Health And Wellness

Font styles to use
Sans Serif

Colors

Designer to choose colors to be used in the design.

Requirements
Must have
• Title: Eliminate Pain and Tightness For Good
• Paragraph: Corvella Motion Studio offers a free 60 minute seminar: "The Busy Walker's Manual for Stretching and Living Lighter."
• What to Expect:
• • Identify the underlying cause of your pain and mobility issues
• • Expose what gets in the way of you moving and feeling better
• • Learn why traditional exercises don’t help and can actually make the problem worse
• • Reveal what your posture is saying and how that impacts you
• • Experience your muscle imbalances through movement tests
• • Discover the training method that realigns your posture, increases your mobility and reduces your pain
• Call to action: RSVP online at corvellamotionstudio.com
Nice to have
• Use a relevant image showing a female dealing with tightness in the low back, legs, etc.
• Emphasize that the seminar is FREE.
• Make the call to action prominent.

```html
<!DOCTYPE html>
<html lang="en">
<head>
<meta charset="utf-8">
<title>Corvella Motion Studio – Free Seminar Flyer</title>
<link href="https://fonts.googleapis.com/css2?family=Bebas+Neue&family=Kalam:wght@700&family=Roboto:wght@400;500;700&display=swap" rel="stylesheet">
<style>
  :root{
    --backdrop:#d9d2cc;
    --paper:#f7f7f9;
    --indigo:#3e4190;
    --orange:#f08a1c;
    --mist:#dcdde8;
    --ink:#454545;
    --white:#ffffff;
  }
  html,body{margin:0;padding:0;overflow:hidden;}
  body{width:1200px;height:1093px;background:var(--backdrop);position:relative;font-family:"Roboto",Arial,sans-serif;}
  .flyer{position:absolute;left:200px;top:30px;width:800px;height:1033px;background:var(--paper);overflow:hidden;box-shadow:0 12px 30px rgba(0,0,0,.18);}
  .flyer__shapes{position:absolute;left:0;top:0;width:800px;height:1033px;}
  .hero-photo{position:absolute;left:50px;top:30px;width:360px;height:440px;border-radius:6px;
    background:radial-gradient(ellipse at 45% 55%, #2fb6e6 0%, #7fcde9 30%, #e8c3a8 55%, #f2f2f4 80%);}
  .brand{position:absolute;left:440px;top:82px;display:flex;align-items:center;gap:12px;}
  .brand__mark{width:28px;height:28px;background:var(--orange);}
  .brand__name{font-weight:500;font-size:27px;color:var(--indigo);letter-spacing:-.3px;white-space:nowrap;}
  .headline{position:absolute;left:450px;top:180px;width:320px;margin:0;font-family:"Kalam",cursive;font-weight:700;font-size:34px;line-height:1.3;color:var(--indigo);text-align:center;white-space:nowrap;}
  .headline__rule{position:absolute;left:480px;top:283px;width:260px;height:4px;background:var(--orange);border-radius:2px;transform:rotate(-3deg);}
  .offer{position:absolute;left:0;top:560px;width:800px;text-align:center;color:var(--white);}
  .offer__title{margin:0;font-family:"Bebas Neue",Impact,sans-serif;font-weight:400;font-size:33px;letter-spacing:.3px;}
  .offer__free{color:var(--orange);}
  .offer__sub{margin:6px 0 0;font-size:16px;}
  .expect{position:absolute;left:80px;top:728px;width:650px;}
  .expect__title{margin:0 0 12px;font-family:"Bebas Neue",Impact,sans-serif;font-weight:400;font-size:28px;line-height:34px;color:var(--indigo);}
  .expect__list{list-style:none;margin:0;padding:0;}
  .expect__item{position:relative;padding-left:38px;font-size:14px;line-height:24px;color:var(--ink);}
  .expect__item svg{position:absolute;left:0;top:4px;width:16px;height:16px;}
  .expect__verb{color:var(--orange);}
  .cta{position:absolute;left:0;top:988px;width:800px;margin:0;text-align:center;font-size:22px;line-height:26px;color:var(--white);}
  .cta__url{color:var(--orange);font-weight:700;}
</style>
</head>
<body>
<article class="flyer">
  <svg class="flyer__shapes" viewBox="0 0 800 1033" aria-hidden="true">
    <path d="M0 500 Q380 610 800 440 L800 690 Q420 610 0 690 Z" fill="var(--indigo)"/>
    <path d="M520 545 Q680 520 800 430 L800 446 Q680 535 520 545 Z" fill="var(--orange)"/>
    <path d="M0 690 Q420 610 800 690 L800 722 Q430 625 0 702 Z" fill="var(--mist)"/>
    <path d="M0 672 Q60 662 140 648 Q60 676 0 694 Z" fill="var(--orange)"/>
    <path d="M0 990 Q380 940 800 955 L800 1033 L0 1033 Z" fill="var(--indigo)"/>
    <path d="M0 978 Q380 928 800 943 L800 955 Q380 940 0 990 Z" fill="var(--mist)"/>
  </svg>

  <div class="hero-photo" role="img" aria-label="Photo of a woman in a blue dress sitting on the floor, rubbing her sore calf, with blue heels beside her"></div>

  <div class="brand">
    <span class="brand__mark"></span>
    <span class="brand__name">Corvella Motion Studio</span>
  </div>

  <h1 class="headline">Eliminate Pain and<br>Tightness For Good</h1>
  <div class="headline__rule"></div>

  <section class="offer">
    <h2 class="offer__title">Corvella Motion Studio offers a <span class="offer__free">free 60 minute seminar</span></h2>
    <p class="offer__sub">The Busy Walker's Manual for Stretching and Living Lighter.</p>
  </section>

  <section class="expect">
    <h3 class="expect__title">What to expect:</h3>
    <ul class="expect__list">
      <li class="expect__item"><svg viewBox="0 0 16 16"><circle cx="8" cy="8" r="6.5" fill="none" stroke="var(--indigo)" stroke-width="1.6"/><path d="M5 8.2 7.2 10.3 11 6" fill="none" stroke="var(--indigo)" stroke-width="1.6"/></svg><span class="expect__verb">Identify</span> the underlying cause of your pain and mobility issues</li>
      <li class="expect__item"><svg viewBox="0 0 16 16"><circle cx="8" cy="8" r="6.5" fill="none" stroke="var(--indigo)" stroke-width="1.6"/><path d="M5 8.2 7.2 10.3 11 6" fill="none" stroke="var(--indigo)" stroke-width="1.6"/></svg><span class="expect__verb">Expose</span> what gets in the way of you moving and feeling better</li>
      <li class="expect__item"><svg viewBox="0 0 16 16"><circle cx="8" cy="8" r="6.5" fill="none" stroke="var(--indigo)" stroke-width="1.6"/><path d="M5 8.2 7.2 10.3 11 6" fill="none" stroke="var(--indigo)" stroke-width="1.6"/></svg><span class="expect__verb">Learn</span> why traditional exercises don’t help and can actually make the problem worse</li>
      <li class="expect__item"><svg viewBox="0 0 16 16"><circle cx="8" cy="8" r="6.5" fill="none" stroke="var(--indigo)" stroke-width="1.6"/><path d="M5 8.2 7.2 10.3 11 6" fill="none" stroke="var(--indigo)" stroke-width="1.6"/></svg><span class="expect__verb">Reveal</span> what your posture is saying and how that impacts you</li>
      <li class="expect__item"><svg viewBox="0 0 16 16"><circle cx="8" cy="8" r="6.5" fill="none" stroke="var(--indigo)" stroke-width="1.6"/><path d="M5 8.2 7.2 10.3 11 6" fill="none" stroke="var(--indigo)" stroke-width="1.6"/></svg><span class="expect__verb">Experience</span> your muscle imbalances through movement tests</li>
      <li class="expect__item"><svg viewBox="0 0 16 16"><circle cx="8" cy="8" r="6.5" fill="none" stroke="var(--indigo)" stroke-width="1.6"/><path d="M5 8.2 7.2 10.3 11 6" fill="none" stroke="var(--indigo)" stroke-width="1.6"/></svg><span class="expect__verb">Discover</span> the training method that realigns your posture, increases your mobility and reduces your pain</li>
    </ul>
  </section>

  <p class="cta">RSVP online at <span class="cta__url">corvellamotionstudio.com</span></p>
</article>
</body>
</html>
```